Marble Orchard - Report on digital habits and attitudes

We are a research company and we have written a PowerPoint Report to present the results of a series of surveys conducted in the last three years. The research is about the "Marble Orchard": people are facing the opportunities and challanges of their lives transformed by the digital technologies. We have investigated a number of topics through thousands of interviews and we've analyzed the data presented in the PowerPoint document.
We're not quite satisfied with the look and feel of the report: it looks too flat and boring, too "basic" to be presented as a professional work, yet being just that. We'd like you to upgrade the graphics and style of the report up to the level of a professional research product. The document still needs to be fully editable (either text and charts) but you can rearrange all the contents as you please, adding images, changing font and text size, colors and whatever you think is necessary to reach our goal.

Target Market(s)

Media covering digital issues
Marketing executives
Public institutions and policy makers

Industry/Entity Type

Market Research

Requirements
Must have
• The treats of a professional work
Fully editable within PowerPoint (either text and charts)
Nice to have
• Smart images
Original organization of the pages
Colors and graphics coherent with the quillbrook.it logo/website look and feel
Should not have
• PPT document over 30 MBytes
Images violating copyright

```html
<!DOCTYPE html>
<html lang="it">
<head>
<meta charset="utf-8">
<title>Osservatorio Marble Orchard – Report</title>
<link rel="stylesheet" href="https://fonts.googleapis.com/css2?family=Tinos&family=Roboto:wght@300;400;500&display=swap">
<style>
:root{
  --page:#ececec;
  --white:#ffffff;
  --ink:#2b2b2b;
  --text:#6b6b6b;
  --orange:#f39a2e;
  --tan:#c9a57a;
  --grey:#a3a3a3;
  --dark:#4a4238;
  --green:#9aaa2e;
  --beige:#fbe8d3;
}
*{margin:0;padding:0;box-sizing:border-box}
html,body{width:1200px;height:4612px;overflow:hidden;background:var(--page)}
body{position:relative;font-family:"Roboto",sans-serif;color:var(--text)}
.slide{position:absolute;left:104px;width:990px;height:566px;background:var(--white);overflow:hidden;box-shadow:0 2px 8px rgba(0,0,0,.12)}
.abs{position:absolute}
.h1{font-family:"Tinos",serif;color:var(--ink);font-weight:400;letter-spacing:.5px}
.title{font-size:38px}
.body{font-size:10.5px;line-height:1.75;font-weight:300;text-align:justify}
.ph{position:absolute}
.brand{position:absolute;display:flex;align-items:center;gap:6px;font-family:"Roboto",sans-serif;font-weight:500;font-size:13px;color:var(--orange)}
.brand i{display:block;width:10px;height:10px;background:var(--orange)}
/* index */
.toc{position:absolute;left:66px;top:122px;width:200px;font-family:"Tinos",serif;font-size:11px;color:var(--ink)}
.toc li{list-style:none;display:flex;justify-content:space-between;height:43px}
.toc b{font-weight:400;color:var(--orange)}
/* bars */
.bars{position:absolute;font-size:8px;font-weight:300}
.bars .row{display:flex;align-items:center;height:17px}
.bars .lab{width:var(--lw);text-align:right;padding-right:6px;white-space:nowrap;overflow:hidden}
.bars .bar{height:11px;color:#fff;font-size:8px;text-align:right;padding-right:4px;line-height:11px}
.bars.dark .bar{background:var(--dark)}
.bars.green .bar{background:var(--green)}
.chartbox{position:absolute;top:200px;width:244px;height:197px;background:#fff;border:2px solid var(--orange)}
.chartbox svg{display:block}
</style>
</head>
<body>

<!-- Cover -->
<section class="slide" style="top:68px;background:linear-gradient(120deg,#f7f7f8,#e9eaee)">
  <div class="ph" role="img" aria-label="Rete digitale di persone connesse su sfondo chiaro con grandi frecce fotografiche verso l'alto" style="left:380px;top:0;width:610px;height:566px;background:linear-gradient(90deg,rgba(233,234,238,0),#c8cdd6 40%,#b59a78 60%,#e6e6ea)"></div>
  <div class="brand" style="left:93px;top:36px"><i></i>Quillbrook</div>
  <div class="abs h1" style="left:93px;top:124px;font-size:64px;line-height:1">OMO</div>
  <div class="abs h1" style="left:93px;top:206px;font-size:36px;line-height:1">OSSERVATORIO SU<br>MARBLE ORCHARD</div>
  <div class="ph" role="img" aria-label="Mano che regge un tablet con icone digitali fluttuanti" style="left:102px;top:300px;width:220px;height:220px;border-radius:50%;background:radial-gradient(circle at 50% 40%,#e6e1ea,#a58c8a 70%,#8a6c55)"></div>
</section>

<!-- Index -->
<section class="slide" style="top:709px">
  <div class="ph" role="img" aria-label="Banda decorativa color sabbia" style="left:150px;top:170px;width:120px;height:396px;background:linear-gradient(180deg,rgba(251,232,211,.2),var(--beige))"></div>
  <div class="abs h1 title" style="left:66px;top:40px">INDICE :</div>
  <div class="brand" style="left:250px;top:52px;font-size:11px"><i></i>Quillbrook</div>
  <ul class="toc">
    <li><span>Capitolo 11</span><b>01</b></li>
    <li><span>Capitolo 1</span><b>04</b></li>
    <li><span>Capitolo 1</span><b>10</b></li>
    <li><span>Capitolo 1</span><b>15</b></li>
    <li><span>Capitolo 1</span><b>20</b></li>
    <li><span>Capitolo 1</span><b>24</b></li>
    <li><span>Capitolo 1</span><b>28</b></li>
  </ul>
  <div class="ph" role="img" aria-label="Mani al tramonto che sorreggono una sfera luminosa di connessioni" style="left:340px;top:0;width:650px;height:566px;background:linear-gradient(180deg,#7fb0a8 0%,#b8b08a 45%,#e99a4a 70%,#3a2a22 100%)"></div>
</section>

<!-- Introduzione -->
<section class="slide" style="top:1349px">
  <div class="ph" role="img" aria-label="Scultura in pietra di una testa da cui sboccia un fiore" style="left:0;top:0;width:408px;height:424px;background:linear-gradient(135deg,#9a9a92,#5c5c56 60%,#3f3f3b)"></div>
  <svg class="abs" style="left:0;top:0" width="990" height="566" aria-hidden="true">
    <defs><linearGradient id="introBand" x1="0" x2="1"><stop offset="0" stop-color="#c9a57a"/><stop offset=".6" stop-color="#f39a2e"/></linearGradient></defs>
    <polygon points="0,420 403,420 408,182 612,566 0,566" fill="url(#introBand)"/>
  </svg>
  <div class="abs h1 title" style="left:455px;top:30px">INTRODUZIONE :</div>
  <p class="abs body" style="left:455px;top:88px;width:505px">Il digitale ha cambiato il mondo a un livello di profondità di cui non siamo ancora pienamente consapevoli. E' facile riconoscere le manifestazioni del digitale nei comportamenti delle persone e notare come ha formato nuove abitudini e ritualità quotidiane.</p>
  <p class="abs body" style="left:455px;top:160px;width:505px">Non è altrettanto immediato comprendere quanto il digitale abbia modificato il mondo interiore e abbia inciso sul senso dell'identità, sulle emozioni in gioco nelle relazioni, su affetti e sessualità, sul modo di concepire la società, i diritti e la libertà personale.</p>
  <p class="abs body" style="left:534px;top:234px;width:426px">L'obiettivo di questo lavoro di ricerca è raccontare la struttura e l'evoluzione di alcuni atteggiamenti di fondo che influenzano i comportamenti quotidiani legati alle tecnologie digitali. Le informazioni sono ricavate dalle dichiarazioni di campioni di individui chiamati a riflettere sull'ambiente connesso, cioè l'insieme di tutte le relazioni e attività che si possono svolgere grazie alla Rete e, più in generale, grazie a tutte le innovazioni introdotte dagli strumenti e dai servizi digitali.</p>
  <p class="abs body" style="left:598px;top:372px;width:362px">L'analisi indaga le dinamiche cognitive e psicologiche che originano i comportamenti e descrive gli orientamenti di base sottostanti alle scelte – talvolta inconsapevoli – che danno forma alla dimensione digitale della vita. Questa, infatti, può assumere una configurazione molto diversa dalla dimensione della vita di prima (a cui ci riferiamo col termine «naturale», intendendo con questo la vita non mediata dagli strumenti dell'ICT): persone introverse nella vita naturale possono avere una vita digitale ricca di relazioni.</p>
</section>

<!-- La ricerca -->
<section class="slide" style="top:1990px">
  <div class="ph" role="img" aria-label="Uomo in giacca che tocca un'interfaccia di icone digitali connesse" style="left:0;top:0;width:408px;height:424px;background:linear-gradient(135deg,#1d3b5c,#4f86b0 50%,#26466a)"></div>
  <div class="ph" role="img" aria-label="Illustrazione dell'evoluzione umana fino all'uomo al computer" style="left:157px;top:320px;width:833px;height:246px;background:linear-gradient(90deg,#a3a3a3,#c9a57a 50%,#f39a2e)"></div>
  <div class="abs h1 title" style="left:455px;top:30px">LA RICERCA :</div>
  <p class="abs body" style="left:455px;top:88px;width:505px">"L'ambiente connesso è tutto ciò che accade perché siamo connessi alla rete: tutti i modi che, grazie alla connessione alla rete, abbiamo per comunicare con altre persone e tessere relazioni, per fruire di contenuti di tutti i tipi (informazioni testuali, video, musica, giochi etc), per acquistare prodotti e utilizzare servizi (bancari, amministrativi, pagamenti), o utilizzare nuove tecnologie per la casa, per la mobilità, per il fitness e la salute, etc...</p>
  <p class="abs body" style="left:455px;top:198px;width:505px">Alcune di queste attività fanno ormai parte della nostra vita quotidiana, altre probabilmente lo diventeranno nei prossimi anni.Ecco, tutto questo compone l'ambiente connesso. La popolazione online riesce quindi a rappresentare quella fetta di società italiana maggiormente impattata dal fenomeno della digitalizzazione e del mondo connesso, anche se con livelli di consapevolezza, stress, paure e atteggiamenti completamente diversi che descrivono «mondi» molto diversi.</p>
</section>

<!-- Le paure 1 -->
<section class="slide" style="top:2629px">
  <div class="abs h1 title" style="left:70px;top:40px">LE PAURE :</div>
  <p class="abs body" style="left:70px;top:100px;width:490px">Il digitale può fare paura per le conseguenze che produce nelle capacità cognitive, nelle relazioni personali e sociali, fino a quelle internazionali. Molti non conoscono cosa c'è dietro e da dove vengono certe magie della tecnologia, alle quali ci siamo abituati e che non ci meravigliano più ma rimangono in gran parte incomprensibili.Inoltre, certi racconti sulla sorveglianza digitale e sui nuovi poteri che emergono dai dati ispirano un senso di sospetto condiviso da un'ampia maggioranza di individui.</p>
  <p class="abs body" style="left:70px;top:210px;width:490px">Il sospetto che il flusso di informazioni generato dalle tecnologie sia utilizzato con finalità di controllo o manipolazione è molto diffuso e riguarda otto individui su dieci.Il 77% si dichiara d'accordo con l'affermazione secondo la quale il digitale crea problemi di socialità nei ragazzi e il dato aumenta tra le</p>
  <div class="bars dark" style="left:0;top:362px;--lw:428px">
    <div class="row"><div class="lab">Nell'ambiente connesso è più facile manipolare le persone</div><div class="bar" style="width:113px">80%</div></div>
    <div class="row"><div class="lab">I ragazzi hanno notevoli problemi di socializzazione a causa del digitale</div><div class="bar" style="width:109px">77%</div></div>
    <div class="row"><div class="lab">Alcuni servizi sanno tutto di noi: chi vediamo, cosa facciamo, cosa scriviamo e diciamo, anche</div><div class="bar" style="width:106px;background:none;color:var(--text);text-align:right;border-left:106px solid var(--dark);padding:0;width:auto"> 75%</div></div>
    <div class="row"><div class="lab">I dispositivi che utilizzo mandano continuamente dati su di me a organizzazioni di cui ignoro</div><div class="bar" style="width:100px">71%</div></div>
    <div class="row"><div class="lab">Le notizie online ci fanno perdere la capacità di distinguere il vero dal falso</div><div class="bar" style="width:99px">70%</div></div>
    <div class="row"><div class="lab">Il digitale diminuisce la capacità di apprendimento a tutte le età</div><div class="bar" style="width:59px">42%</div></div>
    <div class="row"><div class="lab">Le democrazie sono a rischio a causa della diffusione dell'online</div><div class="bar" style="width:49px">35%</div></div>
    <div class="row"><div class="lab">Prossimamente ci sarà una guerra cibernetica fra Stati</div><div class="bar" style="width:47px">33%</div></div>
  </div>
  <div class="abs" style="left:608px;top:45px;width:346px;height:466px;border:3px solid var(--orange)"></div>
  <div class="ph" role="img" aria-label="Coppia sorridente che guarda lo smartphone a un tavolino" style="left:594px;top:55px;width:346px;height:466px;background:linear-gradient(135deg,#e8e4dc,#b9a58c 50%,#7d9db8)"></div>
</section>

<!-- Le paure 2 -->
<section class="slide" style="top:3270px">
  <div class="abs h1 title" style="left:70px;top:40px">LE PAURE :</div>
  <p class="abs body" style="left:70px;top:100px;width:410px">Otto persone su dieci ritengono che nell'ambiente digitale si siano diffuse pratiche di manipolazione delle persone più efficaci rispetto al passato. Il riferimento al passato è relativo al '900, epoca in cui i mezzi di comunicazione di massa, tutti broadcasting, erano gestiti dai governi e dai grandi editori.</p>
  <p class="abs body" style="left:510px;top:100px;width:410px">Il timore che il digitale ostacoli i rapporti e la socialità dei ragazzi è calato durante il primo lockdown, quando alcune formule di relazione digitale hanno «stupito» per essere in grado di</p>
  <div class="abs" style="left:0;top:256px;width:990px;height:127px;background:linear-gradient(90deg,#a3a3a3,#c9a57a 40%,#c9a57a 70%,#f39a2e)"></div>
  <div class="chartbox" style="left:70px">
    <svg width="240" height="193" viewBox="0 0 240 193" font-family="Roboto,sans-serif" font-size="9" fill="#8a8a8a">
      <path d="M20,80 C40,90 60,110 80,120 S110,80 130,72 S180,70 215,68" fill="none" stroke="#888" stroke-width="1.5"/>
      <text x="18" y="76">79%</text><text x="66" y="112">78%</text><text x="112" y="140">77%</text><text x="150" y="82">79%</text><text x="200" y="64">80%</text>
      <line x1="8" y1="176" x2="232" y2="176" stroke="#ddd"/>
      <text x="12" y="188">feb 19</text><text x="58" y="188">ott 19</text><text x="102" y="188">feb 20</text><text x="148" y="188">mag 20</text><text x="196" y="188">nov 20</text>
    </svg>
  </div>
  <div class="chartbox" style="left:370px">
    <svg width="240" height="193" viewBox="0 0 240 193" font-family="Roboto,sans-serif" font-size="9" fill="#8a8a8a">
      <path d="M20,60 C40,62 55,88 70,80 S100,58 115,62 S140,125 160,120 S195,60 210,52" fill="none" stroke="#888" stroke-width="1.5"/>
      <text x="20" y="56">77%</text><text x="65" y="98">75%</text><text x="110" y="58">77%</text><text x="150" y="138">72%</text><text x="200" y="46">77%</text>
      <line x1="8" y1="176" x2="232" y2="176" stroke="#ddd"/>
      <text x="12" y="188">feb 19</text><text x="58" y="188">ott 19</text><text x="102" y="188">feb 20</text><text x="148" y="188">mag 20</text><text x="196" y="188">nov 20</text>
    </svg>
  </div>
  <div class="chartbox" style="left:684px">
    <svg width="240" height="193" viewBox="0 0 240 193" font-family="Roboto,sans-serif" font-size="9" fill="#8a8a8a">
      <path d="M20,120 C40,110 55,100 70,98 S100,108 115,98 S140,52 160,55 S195,80 210,82" fill="none" stroke="#888" stroke-width="1.5"/>
      <text x="14" y="138">72%</text><text x="62" y="116">74%</text><text x="108" y="116">74%</text><text x="152" y="46">77%</text><text x="204" y="98">75%</text>
      <line x1="8" y1="176" x2="232" y2="176" stroke="#ddd"/>
      <text x="12" y="188">feb 19</text><text x="58" y="188">ott 19</text><text x="102" y="188">feb 20</text><text x="148" y="188">mag 20</text><text x="196" y="188">nov 20</text>
    </svg>
  </div>
  <p class="abs body" style="left:70px;top:440px;width:850px">3 rispondenti su 4 (ovvero 30 milioni di individui, metà della popolazione italiana) sono convinti che alcune organizzazioni sappiano tutto di noi, anche quando non siamo online. Il dato era leggermente aumentato nella primavera del 2020 probabilmente come conseguenza del dibattito sulle capacità dei sistemi di tracciamento nel contrastare la diffusione del contagio ma è rientrato ai livelli pre Covid. Questo aspetto è stato incluso tra gli atteggiamenti di sospetto ma il giudizio negativo potrebbe riguardare solo una parte dei cittadini: altri – di cui tuttavia ignoriamo il numero – potrebbero ritenere che il controllo sociale sia un aspetto positivo del digitale.</p>
</section>

<!-- Le speranze -->
<section class="slide" style="top:3910px">
  <div class="abs h1 title" style="left:70px;top:40px">LE SPERANZE :</div>
  <p class="abs body" style="left:70px;top:100px;width:410px">Otto persone su dieci ritengono che nell'ambiente digitale si siano diffuse pratiche di manipolazione delle persone più efficaci rispetto al passato. Il riferimento al passato è relativo al '900, epoca in cui i mezzi di comunicazione di massa, tutti broadcasting, erano gestiti dai governi e dai grandi editori.</p>
  <div class="abs" style="left:0;top:265px;width:475px;height:118px;background:linear-gradient(90deg,#a3a3a3,#c9a57a)"></div>
  <div class="ph" role="img" aria-label="Donna al lavoro con il computer portatile in casa" style="left:72px;top:265px;width:322px;height:118px;background:linear-gradient(90deg,#d9d2c6,#8c7a66 60%,#cfc5b6)"></div>
  <div class="abs" style="left:0;top:383px;width:22px;height:183px;background:#a3a3a3"></div>
  <div class="abs" style="left:0;top:545px;width:990px;height:21px;background:linear-gradient(90deg,#a3a3a3,#c9a57a 40%,#f39a2e)"></div>
  <div class="abs" style="left:970px;top:290px;width:20px;height:276px;background:linear-gradient(180deg,#fbd7a8,#f39a2e)"></div>
  <svg class="abs" style="left:40px;top:390px" width="470" height="160" viewBox="0 0 470 160" font-family="Roboto,sans-serif" font-size="9" fill="#8a8a8a" aria-hidden="true">
    <path d="M20,40 C60,60 80,95 104,95 S180,58 206,48 S270,35 300,38 S370,48 400,50" fill="none" stroke="var(--green)" stroke-width="1.5" stroke-dasharray="2 3"/>
    <g fill="#b8c46a"><circle cx="20" cy="40" r="3.5"/><circle cx="104" cy="95" r="3.5"/><circle cx="206" cy="48" r="3.5"/><circle cx="300" cy="38" r="3.5"/><circle cx="400" cy="50" r="3.5"/></g>
    <text x="8" y="60">53%</text><text x="96" y="115">51%</text><text x="196" y="68">54%</text><text x="290" y="32">55%</text><text x="390" y="70">54%</text>
    <text x="10" y="150">feb 19</text><text x="102" y="150">ott 19</text><text x="198" y="150">feb 20</text><text x="292" y="150">mag 20</text><text x="386" y="150">nov 20</text>
  </svg>
  <p class="abs body" style="left:546px;top:28px;width:414px">Un italiano su due guarda alla diffusione del digitale con un atteggiamento positivo, fiducioso nel fatto che questo fenomeno possa avere un impatto virtuoso su diversi ambiti della vita quotidiana dei cittadini e sulla società. La speranza più diffusa è la semplificazione conseguente al processo di digitalizzazione: il 77% del campione ritiene che il processo di digitalizzazione rende più semplice la vita dei cittadini. Attorno e grazie al digitale si sviluppano inoltre competenze e una generale crescita di conoscenza di cui beneficia tutta la società.</p>
  <p class="abs body" style="left:546px;top:186px;width:414px">La maggioranza dei cittadini ripone una grande fiducia nelle smart technologies che ci si aspetta siano in grado di rendere gli ambienti in cui viviamo (case, città, uffici) dei luoghi migliori, dove vivere con una qualità più elevata. Il tema dell'informazione online, invece, divide la popolazione tra chi</p>
  <p class="abs body" style="left:546px;top:278px;width:414px">online abbia un impatto positivo sul sistema informativo e chi non vede un miglioramento della qualità e della trasparenza dell'informazione. Meno diffuse sono le aspettative riposte negli effetti positivi delle tecnologie digitali in ambito sanitario, sul funzionamento del sistema democratico e</p>
  <div class="bars green" style="left:546px;top:398px;--lw:194px;font-size:6.5px">
    <div class="row" style="height:13px"><div class="lab">La digitalizzazione semplifica la vita ai cittadini</div><div class="bar" style="width:68px;height:9px;line-height:9px">77%</div></div>
    <div class="row" style="height:13px"><div class="lab">Chi si impegna nel digitale ottiene nuove competenze</div><div class="bar" style="width:63px;height:9px;line-height:9px">72%</div></div>
    <div class="row" style="height:13px"><div class="lab">Le case smart alzano la qualità della vita in casa</div><div class="bar" style="width:58px;height:9px;line-height:9px">66%</div></div>
    <div class="row" style="height:13px"><div class="lab">Le città smart migliorano la vita urbana</div><div class="bar" style="width:56px;height:9px;line-height:9px">63%</div></div>
    <div class="row" style="height:13px"><div class="lab">L'informazione online rende il sistema più trasparente</div><div class="bar" style="width:50px;height:9px;line-height:9px">57%</div></div>
    <div class="row" style="height:13px"><div class="lab">Il digitale aiuta a prevenire e curare meglio le malattie</div><div class="bar" style="width:43px;height:9px;line-height:9px">49%</div></div>
    <div class="row" style="height:13px"><div class="lab">Più informazione online rafforza la partecipazione democratica</div><div class="bar" style="width:39px;height:9px;line-height:9px">45%</div></div>
    <div class="row" style="height:13px"><div class="lab">Il lavoro sarà più equo grazie alla digitalizzazione</div><div class="bar" style="width:32px;height:9px;line-height:9px">37%</div></div>
  </div>
</section>

</body>
</html>
```